FunBrixo Business Card

We need a business card design for our company. We sell construction-themed amusement rides for kids.

Contact Information for Business Card

Contact info on business card should include:
Carl Dunning
Co-Founder & COO
(833) 571-FUNBRIX
Carl@funbrixo-demo.com
www.funbrixo-demo.com

```html
<!DOCTYPE html>
<html lang="en">
<head>
<meta charset="utf-8">
<title>FunBrixo Business Card</title>
<link rel="stylesheet" href="https://fonts.googleapis.com/css2?family=Lato:wght@400;700;900&display=swap">
<style>
  :root {
    --stage: #3a3b3d;
    --card-black: #0b0a0b;
    --card-white: #ffffff;
    --brand-orange: #f07623;
    --brand-purple: #8e3a9d;
    --ink-dark: #1e1e1e;
    --ink-light: #ffffff;
  }
  * { margin: 0; padding: 0; box-sizing: border-box; }
  html, body { width: 1200px; height: 900px; overflow: hidden; }
  body {
    background: var(--stage);
    font-family: "Lato", sans-serif;
    position: relative;
  }
  .card {
    position: absolute;
    width: 640px;
    height: 366px;
    border-radius: 28px;
    overflow: hidden;
    box-shadow: 0 14px 30px rgba(0,0,0,0.45);
  }
  .card-back {
    left: 120px;
    top: 52px;
    background: var(--card-black);
    display: flex;
    align-items: center;
    justify-content: center;
  }
  .card-front {
    left: 440px;
    top: 482px;
    background: var(--card-white);
  }
  .brand-name {
    font-weight: 900;
    color: var(--brand-orange);
    letter-spacing: 0.5px;
    line-height: 1;
  }
  .card-back .brand-name { font-size: 72px; }
  .card-front .brand-name {
    position: absolute;
    left: 78px;
    top: 120px;
    font-size: 50px;
  }
  .wave {
    position: absolute;
    inset: 0;
    width: 100%;
    height: 100%;
  }
  .identity {
    position: absolute;
    right: 56px;
    top: 44px;
    text-align: right;
  }
  .identity-name {
    font-weight: 900;
    font-size: 30px;
    line-height: 1.15;
    color: var(--brand-orange);
    text-transform: uppercase;
    letter-spacing: 0.5px;
  }
  .identity-title {
    font-size: 17px;
    color: var(--ink-dark);
    margin-top: 2px;
  }
  .contact-list {
    position: absolute;
    right: 28px;
    top: 200px;
    list-style: none;
  }
  .contact-item {
    display: flex;
    align-items: center;
    justify-content: flex-end;
    gap: 14px;
    height: 34px;
    font-size: 17px;
    color: var(--ink-light);
  }
  .contact-icon { width: 20px; height: 20px; flex: none; }
</style>
</head>
<body>
  <section class="card card-back" aria-label="Card back">
    <span class="brand-name">FunBrixo</span>
  </section>

  <section class="card card-front" aria-label="Card front">
    <svg class="wave" viewBox="0 0 640 366" preserveAspectRatio="none" aria-hidden="true">
      <path d="M0,300 C190,300 320,250 400,200 C470,160 540,150 640,146 L640,366 L0,366 Z" fill="var(--card-black)"/>
      <path d="M0,286 C185,286 305,238 388,186 C450,148 510,136 570,134" fill="none" stroke="var(--brand-orange)" stroke-width="11" stroke-linecap="round"/>
    </svg>

    <span class="brand-name">FunBrixo</span>

    <div class="identity">
      <p class="identity-name">Carl Dunning</p>
      <p class="identity-title">Co-Founder &amp; COO</p>
    </div>

    <ul class="contact-list">
      <li class="contact-item">
        <span>(833) 571-FUNBRIX</span>
        <svg class="contact-icon" viewBox="0 0 24 24" aria-hidden="true">
          <path d="M6.6 10.8a15.1 15.1 0 0 0 6.6 6.6l2.2-2.2a1 1 0 0 1 1-.25 11.4 11.4 0 0 0 3.6.57 1 1 0 0 1 1 1V20a1 1 0 0 1-1 1A17 17 0 0 1 3 4a1 1 0 0 1 1-1h3.5a1 1 0 0 1 1 1c0 1.25.2 2.45.57 3.57a1 1 0 0 1-.25 1z" fill="var(--brand-purple)"/>
        </svg>
      </li>
      <li class="contact-item">
        <span>Carl@funbrixo-demo.com</span>
        <svg class="contact-icon" viewBox="0 0 24 24" aria-hidden="true">
          <rect x="2" y="5" width="20" height="14" rx="1.5" fill="var(--brand-purple)"/>
          <path d="M3 6l9 7 9-7" fill="none" stroke="var(--card-black)" stroke-width="1.6"/>
        </svg>
      </li>
      <li class="contact-item">
        <span>www.funbrixo-demo.com</span>
        <svg class="contact-icon" viewBox="0 0 24 24" aria-hidden="true">
          <circle cx="12" cy="12" r="10" fill="var(--brand-purple)"/>
          <g fill="none" stroke="var(--card-black)" stroke-width="1.3">
            <ellipse cx="12" cy="12" rx="4.5" ry="10"/>
            <path d="M2 12h20M4 7h16M4 17h16"/>
          </g>
        </svg>
      </li>
    </ul>
  </section>
</body>
</html>
```